Wattle Kitchen logo

I am a catering and food business that requires a logo for my website and all related business branding. I also need a label for my hot sauce. You can find my information on Facebook and there is a picture of the logo I currently use and also a bottle of my hot sauce.
I am based in the Adelaide Hills in South Australia. I would like to use black and gold or Purple and gold my colour scheme and really like the hornet cartoon that I currently use. Something more refined and original would be great...
Catering

```html
<!DOCTYPE html>
<html lang="en">
<head>
<meta charset="utf-8">
<title>Wattle Kitchen Logo and Wattle Sauce Label</title>
<link rel="stylesheet" href="https://fonts.googleapis.com/css2?family=Arimo&family=Barlow:wght@500&family=Oswald:wght@400;500;600&family=Russo+One&display=swap">
<style>
  :root {
    --ink: #231f20;
    --paper: #ffffff;
    --gold: #f2cb1d;
    --frame: #8a8a8a;
  }
  * { margin: 0; padding: 0; box-sizing: border-box; }
  html, body { width: 1200px; height: 1000px; overflow: hidden; background: var(--paper); }
  .canvas { position: relative; width: 1200px; height: 1000px; color: var(--ink); }

  .brand-mark {
    position: absolute;
    border: 3px solid var(--ink);
    border-radius: 50%;
    display: flex; flex-direction: column; align-items: center; justify-content: center;
    font-family: "Oswald", sans-serif; font-weight: 500; color: var(--ink);
    text-transform: uppercase; text-align: center; line-height: 1.05;
  }
  .brand-mark--primary { left: 188px; top: 272px; width: 270px; height: 270px; font-size: 46px; letter-spacing: 3px; }
  .brand-mark--label { left: 846px; top: 138px; width: 124px; height: 124px; border-width: 2px; font-size: 21px; letter-spacing: 1.5px; }
  .brand-mark--footer { left: 731px; top: 831px; width: 54px; height: 54px; border-width: 1.5px; font-size: 9px; letter-spacing: .5px; }

  .caption {
    position: absolute; left: 120px; top: 879px;
    font-family: "Arimo", sans-serif; font-size: 18px; line-height: 22px;
  }

  .label {
    position: absolute; left: 701px; top: 80px; width: 414px; height: 842px;
    border: 1px solid var(--frame);
  }
  .label__tagline {
    position: absolute; left: 0; width: 100%; top: 248px; text-align: center;
    font-family: "Oswald", sans-serif; font-weight: 400; font-size: 17px; letter-spacing: 3.2px;
  }
  .label__product {
    position: absolute; left: 63px; top: 272px;
    font-family: "Russo One", sans-serif; font-size: 62px; line-height: 62px; letter-spacing: 3px;
  }
  .label__accent {
    position: absolute; left: 318px; top: 343px; width: 44px; height: 44px;
    border-radius: 50%; background: var(--gold);
  }
  .label__uses {
    position: absolute; left: 63px; top: 412px; width: 302px;
    border-top: 2px solid var(--ink); border-bottom: 2px solid var(--ink);
    padding: 4px 0 3px; text-align: center;
  }
  .label__uses-list { display: block; font-family: "Barlow", sans-serif; font-weight: 500; font-size: 17.5px; letter-spacing: .4px; line-height: 22px; }
  .label__uses-lead { display: block; font-family: "Oswald", sans-serif; font-weight: 600; font-size: 23px; line-height: 28px; letter-spacing: .3px; }

  .label__facts {
    position: absolute; left: 104px; top: 505px; width: 222px; height: 111px;
    border: 1px solid var(--ink); padding: 10px 12px;
    font-family: "Oswald", sans-serif; font-size: 11.5px; line-height: 17px;
  }
  .label__ingredients { text-align: justify; text-align-last: justify; }
  .label__volume { margin-top: 6px; text-align: center; font-size: 19px; }

  .label__origin {
    position: absolute; left: 0; width: 100%; top: 640px; text-align: center;
    font-family: "Barlow", sans-serif; font-weight: 500; font-size: 15.5px; line-height: 20px; letter-spacing: 1px;
  }
  .label__address {
    position: absolute; left: 91px; top: 778px;
    font-family: "Oswald", sans-serif; font-size: 13px; letter-spacing: .8px;
  }
</style>
</head>
<body>
<main class="canvas">
  <div class="brand-mark brand-mark--primary">Wattle<br>Kitchen</div>

  <p class="caption">Wattle Kitchen Logo and Wattle Sauce Label<br>Label designed at 2”x4”. Size can be adjusted.</p>

  <section class="label">
    <div class="brand-mark brand-mark--label" style="left:145px;top:58px;">Wattle<br>Kitchen</div>

    <p class="label__tagline">SOUTHERN AUSTRALIA'S FINEST</p>
    <h1 class="label__product">WATTLE<br>SAUCE</h1>
    <div class="label__accent" role="img" aria-label="Brand mascot accent"></div>

    <p class="label__uses">
      <span class="label__uses-list">HOT SAUCE, MARINADE, CONDIMENT</span>
      <span class="label__uses-lead">&amp; EXTREME FLAVOUR BRINGER</span>
    </p>

    <div class="label__facts">
      <p class="label__ingredients">INGREDIENTS: CAPSICUM, WATER, VINEGAR, SUGAR, GARLIC, LEMON JUICE, OLIVE OIL, CHILLI, SPICES, CORNSTARCH, ALMOND, SALT.</p>
      <p class="label__volume">250 ML</p>
    </div>

    <p class="label__origin">PRODUCT OF AUSTRALIA<br>BEST BEFORE: FEB. 2013</p>

    <div class="brand-mark brand-mark--footer" style="left:29px;top:750px;">Wattle<br>Kitchen</div>
    <p class="label__address">48 ORCHARD LANE. STONEBRIDGE, S.A. 5299</p>
  </section>
</main>
</body>
</html>
```